IT Company needs Website for new Web and Mobile products for Sports and Fitness

Background:

We developed web based white label frontend web solution, backend services and white label mobile apps for to log, analyze, share and control sport and fitness activities. The name of this product suite is "Trevantix" (http://trevantix-example.com)

This products will be used by customers that provide platforms and community systems for sport and fitness. One of the major USP's is, that our technology i open for nearly all common formats, devices and apps out in the market. This means, you can just upload your data directly from device, file or app - e.G. Kestrel, Bolvane, Ravelo, StrideVault, Pacelumo, Zembra and much others.

Two current concrete examples/References

(1) MyQuorel
It's an international platform from quorel for runners. It provides individual training lans and a training log. MyQuorel uses the Backend Product "Trevantix Hub" (see http://hub.trevantix-example.net for a landing page) to integrate device, file and app support. Before this, every user has to track his training with manual inputs

(2) Paceharbor and fen-zine
Both are German customers. Paceharor is focused on runners. fen-zine is focused on Triatheletes. Both use the Product "Trevantix Web". This is a complete web solution with web based frontend solutions for athletes and coaches.

What do we need?
We need website layout for B2B for our products. We don't need lot's of pages. We need the pretty and nice layout, so we can derive the pages we need.

IMPORTANT
We don't talk about the webpages for the product itself (this will be a different project in future). We talk about a website, explaining the products)
Updates

Hi all,

we just start reviewing the first designs, and try to give feedback as detailed as possible. We attached a PDF document, to describe the the products a little bit more detailed. 

As written in the description, in the end we have two different sections. One is the usual stuff like "start page", "about", "contact", "disclaimer", "pricing", "blah...." and one will be the Developer Section, the "Tec Section". This ist aimed to developers (of our customers) that will integrate our products in there existing system or which will integrate our services in there own software.  This "pages" are more like "documentation", so easy to read and cool to look at (cause developers likes it cool, but straight)

Dear all,

we just do the final review. Cause this week is with heavy load, it takes some time...

Cheers

Odell

Target Market(s)

* Platforms and Communities for sport, health and fitness
* Gyms

Industry/Entity Type

Concrete

Font styles to use
Sans Serif

Requirements
Must have
• * Templates shall base on bootstrap. If not, it shall be easily realized on our site with bootstrap or out of the box "full responsive"

* HTML5 / CSS3
Nice to have
• PAGES
- Start Page
- Generic Template (from which we can derive additional pages)
- Contact Page
- Disclaimer Page
- Blog/News Page
- "About us" Page (can be combined with disclaimer)
- One Example product page (in end we have 3 products), shall show (if you need product details, let me know)
- product and it's description
- pricing information
- Add-Ons for the product
- Developer Section Page (Start Point for developers, where the finde "basic technical concepts and developer API's
- Example Developer Page for technical concept
- Example Developer Page for API

LOGO ISSUE
You can use an align to the Logo attached OR provide a new logo. The given logo is a logo for our own B2C Website http://trevantix-example.net. It's not really necessary, that the logo or the color must be used for the product website. Maybe it will be better if it's a complete new one, to avoid irritation between Trevantix as a B2B product and trevantix-example.net as a B2C platform.
Should not have
• No Flash and other proprietary technologies

```html
<!DOCTYPE html>
<html lang="en">
<head>
<meta charset="utf-8">
<title>Trevantix — Backend Services</title>
<link rel="stylesheet" href="https://fonts.googleapis.com/css2?family=Open+Sans:wght@400;600;700&display=swap">
<style>
  :root {
    --brand-blue: #1b6fe0;
    --text-dark: #333638;
    --text-body: #444;
    --nav-text: #2f3133;
    --rule: #dcdcdc;
    --header-bg: #ffffff;
    --hero-bg-light: #f4f4f4;
    --hero-bg-mid: #e6e6e4;
    --btn-grey: #6a6a6a;
  }
  * { box-sizing: border-box; margin: 0; padding: 0; }
  html, body { width: 1200px; height: 481px; overflow: hidden; }
  body { font-family: "Open Sans", Arial, sans-serif; color: var(--text-body); position: relative; background: var(--hero-bg-light); }

  .hero {
    position: absolute; inset: 0;
    background:
      radial-gradient(ellipse 260px 180px at 560px 220px, rgba(200,200,180,0.55), transparent 70%),
      radial-gradient(ellipse 300px 260px at 320px 330px, rgba(210,205,200,0.5), transparent 70%),
      linear-gradient(90deg, var(--hero-bg-light) 0%, var(--hero-bg-mid) 55%, #efefef 100%);
  }

  .site-header {
    position: absolute; top: 0; left: 0; width: 1200px; height: 70px;
    background: var(--header-bg);
    box-shadow: 0 2px 6px rgba(0,0,0,0.08);
    z-index: 3;
  }
  .brand {
    position: absolute; left: 46px; top: 12px;
    display: flex; align-items: center; gap: 8px;
    font-size: 24px; font-weight: 700; color: var(--brand-blue); letter-spacing: 0.2px;
  }
  .brand-mark { width: 14px; height: 14px; background: var(--brand-blue); }

  .main-nav { position: absolute; top: 22px; left: 608px; display: flex; }
  .main-nav a {
    font-size: 13px; font-weight: 600; color: var(--nav-text); text-decoration: none;
    text-transform: uppercase; margin-right: 33px; line-height: 18px;
  }
  .main-nav a.is-active { color: var(--brand-blue); }

  .dropdown {
    position: absolute; left: 924px; top: 60px; width: 171px;
    background: #fff; box-shadow: 0 2px 6px rgba(0,0,0,0.12); z-index: 4;
  }
  .dropdown a {
    display: block; height: 37px; line-height: 37px; padding-left: 15px;
    font-size: 11px; color: var(--text-dark); text-decoration: none; text-transform: uppercase;
    border-bottom: 1px solid #ececec;
  }
  .dropdown a:last-child { border-bottom: none; }

  .hero-photo {
    position: absolute; left: 630px; top: 95px; width: 440px; height: 386px;
    background: linear-gradient(180deg, #d8c6bc 0%, #c9b2a6 35%, #2d3447 60%, #252b3b 100%);
    border-radius: 200px 200px 0 0;
    opacity: 0.9;
  }

  .hero-copy { position: absolute; left: 55px; top: 145px; width: 518px; z-index: 2; }
  .hero-kicker { font-size: 21px; font-weight: 400; color: var(--text-dark); line-height: 30px; white-space: nowrap; }
  .hero-title { margin-top: 8px; font-size: 50px; font-weight: 700; color: var(--brand-blue); line-height: 62px; letter-spacing: 0.5px; white-space: nowrap; }
  .hero-rule { height: 1px; background: var(--rule); }
  .hero-rule.top { margin-top: 14px; }
  .hero-text { margin: 22px 0 24px; font-size: 15px; line-height: 24px; color: var(--text-body); }

  .hero-actions { position: absolute; left: 55px; top: 403px; display: flex; gap: 19px; z-index: 2; }
  .btn {
    height: 44px; display: flex; align-items: center; justify-content: center; gap: 10px;
    font-size: 16px; text-transform: uppercase; border-radius: 2px; background: transparent;
  }
  .btn-primary { width: 173px; border: 1px solid var(--brand-blue); color: var(--brand-blue); }
  .btn-secondary { width: 157px; border: 1px solid var(--btn-grey); color: var(--btn-grey); }
</style>
</head>
<body>
  <div class="hero"></div>

  <header class="site-header">
    <div class="brand"><span class="brand-mark"></span>Trevantix</div>
    <nav class="main-nav">
      <a href="#" class="is-active">Home</a>
      <a href="#">Pages</a>
      <a href="#">Features</a>
      <a href="#">Portfolio</a>
      <a href="#" class="is-active">Blog</a>
      <a href="#">Contact</a>
    </nav>
  </header>

  <div class="dropdown">
    <a href="#">With large image</a>
    <a href="#">With small image</a>
    <a href="#">Single post</a>
  </div>

  <div class="hero-photo" role="img" aria-label="Photo of a smiling businesswoman in a navy pinstripe blazer, seated with hands folded"></div>

  <section class="hero-copy">
    <p class="hero-kicker">We Developed Web Based Frontend Web Solution,Mobile Apps</p>
    <h1 class="hero-title">BACKEND SERVICES</h1>
    <div class="hero-rule top"></div>
    <p class="hero-text">Many desktop publishing packages and web page editors now use the lorem Ipsum as their default model text, and a search for 'lorem ipsum will uncover many web sites still in their infancy.</p>
    <div class="hero-rule"></div>
  </section>

  <div class="hero-actions">
    <a class="btn btn-primary">
      <svg width="14" height="14" viewBox="0 0 14 14"><path d="M13 1 L1 6 L6 8 L8 13 Z" fill="var(--brand-blue)"/></svg>
      Get Started
    </a>
    <a class="btn btn-secondary">
      <svg width="16" height="15" viewBox="0 0 16 15" fill="none" stroke="var(--btn-grey)" stroke-width="1.3" stroke-linejoin="round"><rect x="1" y="6" width="3" height="8"/><path d="M4 7 L7 2 Q8.5 1 8.5 3 L8 6 H13.5 Q15 6 14.5 7.5 L13 13 Q12.6 14 11.5 14 H4"/></svg>
      Buy Now!
    </a>
  </div>
</body>
</html>
```